Brell Stone Company Business Cards

Front and Back Business Card - logo and text setup - cool design. I need workable photoshop or illustrator files so I can setup each employee card with design that is created
Updates

Hi everyone, thank you for the great entries. Please no more white and blue cards - there are so many already - black and silver only now please. thanks!

Target Market(s)

Construction Industry - Facility Managers

Industry/Entity Type

Construction

Contact Information for Business Card

I really like contemporary simplistic looks - clean neat....not opposed to seeing some black backrounds

Requirements
Must have
• Logo/website address with design on front only - www.brellstone-example.com (logo attached)
• Back:
• Name/Title/Company Address/Phone/email address
Nice to have
• Cool design
Should not have
• Nothing gimmicky like Fire or Water - since we are a Fire Protection company - it has all been done

```html
<!DOCTYPE html>
<html lang="en">
<head>
<meta charset="utf-8">
<title>Brell Stone Company – Business Cards</title>
<link rel="stylesheet" href="https://fonts.googleapis.com/css2?family=Lato:wght@400;700;900&display=swap">
<style>
  :root {
    --backdrop: #1c1c1c;
    --card-black: #131313;
    --card-black-mark: #2c2c2c;
    --card-black-back: #151515;
    --silver-bright: #e2e2e5;
    --silver: #c4c4c8;
    --silver-muted: #9c9ca2;
    --hairline: #3a3a3e;
  }
  * { box-sizing: border-box; margin: 0; padding: 0; }
  html, body {
    width: 1200px;
    height: 800px;
    overflow: hidden;
    background: var(--backdrop);
    font-family: "Lato", Arial, sans-serif;
  }
  .stage {
    position: relative;
    width: 1200px;
    height: 800px;
  }
  .card {
    position: absolute;
    width: 318px;
    height: 528px;
  }
  .card--front {
    left: 258px;
    top: 110px;
    background: var(--card-black);
    display: flex;
    align-items: center;
    justify-content: center;
  }
  .card--back {
    left: 628px;
    top: 115px;
    background: var(--card-black-back);
    box-shadow: inset 0 0 0 1px var(--hairline);
    padding: 58px 0 0 40px;
  }
  .brand-name {
    font-weight: 900;
    font-size: 40px;
    line-height: 1;
    letter-spacing: -0.5px;
    white-space: nowrap;
  }
  .card--front .brand-name {
    color: var(--card-black-mark);
    font-size: 46px;
    margin-top: -10px;
  }
  .card--back .brand-name {
    color: var(--silver-bright);
  }
  .person {
    margin-top: 46px;
  }
  .person__name {
    color: var(--silver-bright);
    font-weight: 700;
    font-size: 25px;
    line-height: 1.1;
  }
  .person__title {
    color: var(--silver-muted);
    font-weight: 700;
    font-size: 17px;
    line-height: 1.25;
  }
  .contact {
    position: absolute;
    left: 40px;
    top: 315px;
    color: var(--silver);
    font-size: 16px;
    line-height: 19px;
  }
  .contact__address { margin-bottom: 10px; }
  .contact__lines p { line-height: 21px; }
  .contact__web { margin-top: 19px; letter-spacing: 0.6px; }
</style>
</head>
<body>
  <main class="stage">
    <section class="card card--front" aria-label="Card front">
      <p class="brand-name">Brell Stone</p>
    </section>

    <section class="card card--back" aria-label="Card back">
      <p class="brand-name">Brell Stone</p>

      <div class="person">
        <p class="person__name">Daniel Marsh</p>
        <p class="person__title">CEO/Founder</p>
      </div>

      <div class="contact">
        <p class="contact__address">48 Harbor Lane,<br>Millbrook,<br>NY 10000</p>
        <div class="contact__lines">
          <p>P. (555) 014-2281</p>
          <p>F. (555) 014-2282</p>
          <p>info@brellstone-example.com</p>
        </div>
        <p class="contact__web">www.brellstone-example.com</p>
      </div>
    </section>
  </main>
</body>
</html>
```